New signage for apartment community in the Pacific Northwest

Signage for an apartment community in the Pacific Northwest. It should have a contemporary northwest vibe with a fresh exciting feeling. We are open to the colors cayenne, white, charcoal and a splash of lime green. Sign to have the name 'VOLTE' with the address number 28351 smaller underneath. sign can include a shape under the name or a feeling of energy in the shape of the name.

Target Market(s)

Young urban professionals

Industry/Entity Type

Real Estate Development

Requirements
Must have
• eyecatching
Should not have
• anything too cute or too busy

```html
<!DOCTYPE html>
<html lang="en">
<head>
<meta charset="utf-8">
<title>VOLTE – Community Sign</title>
<link rel="stylesheet" href="https://fonts.googleapis.com/css2?family=Open+Sans:wght@700;800&display=swap">
<style>
  :root {
    --charcoal: #36424d;
    --lime: #00ff00;
    --lime-light: #6dff5a;
    --white: #ffffff;
    --backdrop: #e9ebe8;
  }
  * { box-sizing: border-box; margin: 0; padding: 0; }
  html, body {
    width: 1200px;
    height: 2503px;
    overflow: hidden;
    background: var(--backdrop);
    font-family: "Open Sans", Arial, sans-serif;
  }
  .sign {
    position: absolute;
    left: 100px;
    top: 585px;
    width: 1000px;
    height: 1333px;
    background: var(--charcoal);
  }
  .name-panel {
    position: absolute;
    left: 52px;
    top: 257px;
    width: 901px;
    height: 451px;
    background: var(--lime);
    border-radius: 22px;
    box-shadow: 0 40px 30px -22px rgba(0,0,0,0.45);
  }
  .name-panel-frame {
    position: absolute;
    inset: 18px;
    border: 3px solid var(--charcoal);
    border-radius: 6px;
  }
  .community-name {
    position: absolute;
    left: 0;
    right: 0;
    top: 68px;
    text-align: center;
    font-weight: 800;
    font-size: 262px;
    line-height: 1;
    letter-spacing: -6px;
    color: var(--charcoal);
  }
  .address-pill {
    position: absolute;
    left: 173px;
    top: 322px;
    width: 555px;
    height: 77px;
    background: var(--white);
    border-radius: 39px;
    display: flex;
    align-items: center;
    justify-content: center;
    gap: 14px;
    font-weight: 700;
    font-size: 39px;
    color: var(--charcoal);
  }
  .address-pill svg { width: 28px; height: 36px; }
  .call-label {
    position: absolute;
    left: 0;
    right: 0;
    top: 908px;
    text-align: center;
    font-weight: 700;
    font-size: 110px;
    line-height: 1.1;
    color: var(--white);
  }
  .phone-pill {
    position: absolute;
    left: 175px;
    top: 1059px;
    width: 693px;
    height: 146px;
    border-radius: 73px;
    border: 5px solid var(--white);
    background: linear-gradient(180deg, var(--lime-light) 0%, var(--lime) 45%, #00e000 100%);
    display: flex;
    align-items: center;
    justify-content: flex-end;
    padding-right: 50px;
    font-weight: 800;
    font-size: 86px;
    letter-spacing: -1px;
    color: var(--charcoal);
  }
  .phone-badge {
    position: absolute;
    left: 132px;
    top: 1080px;
    width: 104px;
    height: 104px;
    border-radius: 50%;
    background: var(--white);
    box-shadow: 4px 4px 6px rgba(0,0,0,0.25);
    display: flex;
    align-items: center;
    justify-content: center;
  }
  .phone-badge-ring {
    width: 84px;
    height: 84px;
    border-radius: 50%;
    border: 3px solid var(--charcoal);
    display: flex;
    align-items: center;
    justify-content: center;
  }
  .phone-badge svg { width: 50px; height: 50px; }
</style>
</head>
<body>
  <main class="sign">
    <section class="name-panel">
      <div class="name-panel-frame"></div>
      <h1 class="community-name">VOLTE</h1>
      <p class="address-pill">
        <svg viewBox="0 0 24 32" aria-hidden="true">
          <path d="M12 1C6 1 2 5.5 2 11c0 7.5 10 19 10 19s10-11.5 10-19C22 5.5 18 1 12 1z" fill="none" stroke="#36424d" stroke-width="3.5"/>
          <circle cx="12" cy="11" r="3.5" fill="#36424d"/>
        </svg>
        <span>28351 Pacific Northwest</span>
      </p>
    </section>

    <p class="call-label">Call Now</p>
    <p class="phone-pill">5550-312-846</p>
    <div class="phone-badge">
      <div class="phone-badge-ring">
        <svg viewBox="0 0 24 24" aria-hidden="true">
          <path d="M6.6 10.8c1.4 2.8 3.8 5.1 6.6 6.6l2.2-2.2c.3-.3.7-.4 1-.2 1.1.4 2.3.6 3.6.6.6 0 1 .4 1 1V20c0 .6-.4 1-1 1C10.6 21 3 13.4 3 4c0-.6.4-1 1-1h3.5c.6 0 1 .4 1 1 0 1.3.2 2.5.6 3.6.1.3 0 .7-.2 1L6.6 10.8z" fill="#36424d"/>
          <path d="M14 3.5a7 7 0 0 1 6.5 6.5M14 7a3.5 3.5 0 0 1 3 3" fill="none" stroke="#36424d" stroke-width="1.8" stroke-linecap="round"/>
        </svg>
      </div>
    </div>
  </main>
</body>
</html>
```